Business Card Design Project

Lorabelle is a women fashion house focusing on youthful glamour.

We bring together unique designs, premium quality materials and top craftsmanship to deliver sophisticated yet playful glamour, fun and excitement to the confident woman.

We can sum up the brand identity in 3 words:
Glamour – Sophistication – Unique

Industry/Entity Type

Fashion

Requirements
Must have
• Nim Ferrasco
nim.ferrasco@lorabelle-example.com
Mobile: 081 536 2947
Instragram: lorabelle_label
Facebook: lorabelle

Creative Director
Lorabelle Co., LTD
TEL: 02 631 48 97
42 Maple Row, 2nd Floor , D Building , Thonrak , Chaloemrat 28.
East Sanphet , Rattana , Bangkok 10240 Thailand
www.lorabelle-example.com

```html
<!DOCTYPE html>
<html lang="en">
<head>
<meta charset="utf-8">
<title>Lorabelle Business Card</title>
<link href="https://fonts.googleapis.com/css2?family=Barlow:wght@400;500;600&display=swap" rel="stylesheet">
<style>
  :root {
    --bg: #ecebe7;
    --paper: #ffffff;
    --ink: #3a3a3a;
    --teal: #3aa58b;
    --teal-light: #5cc3a8;
    --teal-dark: #218a72;
    --ornament-light: #d9efe8;
    --tab: #3b3b3d;
    --tab-text: #f2f2f2;
  }
  * { margin: 0; padding: 0; box-sizing: border-box; }
  html, body { width: 1200px; height: 1023px; overflow: hidden; }
  body {
    background: var(--bg);
    font-family: "Barlow", Arial, sans-serif;
    position: relative;
  }
  .card {
    position: absolute;
    width: 560px;
    height: 320px;
    border-radius: 4px;
    overflow: hidden;
    box-shadow: 0 6px 18px rgba(0,0,0,0.12);
  }
  .brand-lockup {
    position: absolute;
    display: flex; flex-direction: column; align-items: flex-end;
  }
  .brand-name { font-weight: 600; line-height: 1; }
  .brand-suffix { font-weight: 500; line-height: 1.2; }

  /* Front */
  .card-front { left: 320px; top: 130px; background: var(--paper); }
  .card-front .ornament {
    position: absolute; right: 0; top: 0; width: 330px; height: 220px;
    background: radial-gradient(ellipse at 70% 30%, var(--ornament-light), rgba(255,255,255,0) 70%);
  }
  .card-front .brand-lockup { left: 34px; top: 34px; color: var(--teal); }
  .card-front .brand-name { font-size: 46px; }
  .card-front .brand-suffix { font-size: 12px; margin-top: 1px; }
  .person { position: absolute; left: 36px; top: 104px; }
  .person-name { color: var(--teal); font-weight: 600; font-size: 21px; line-height: 1.1; }
  .person-title { color: var(--ink); font-size: 13px; margin-top: 2px; }
  .contacts { position: absolute; left: 36px; top: 158px; list-style: none; }
  .contacts li {
    display: flex; align-items: flex-start; gap: 8px;
    color: var(--ink); font-size: 12px; line-height: 16px;
  }
  .contacts svg { width: 11px; height: 11px; margin-top: 2.5px; flex: none; }
  .contacts .gap { margin-top: 5px; }

  /* Back */
  .card-back {
    left: 320px; top: 560px;
    background: linear-gradient(135deg, var(--teal-dark), var(--teal-light) 45%, var(--teal) 100%);
  }
  .card-back .ornament {
    position: absolute; right: 0; top: 60px; width: 300px; height: 260px;
    background: radial-gradient(ellipse at 60% 60%, rgba(255,255,255,0.22), rgba(255,255,255,0) 70%);
  }
  .tagline-tab {
    position: absolute; left: 0; top: 0; width: 40px; height: 270px;
    background: var(--tab); border-bottom-right-radius: 10px;
    display: flex; align-items: center; justify-content: center;
  }
  .tagline {
    transform: rotate(90deg); white-space: nowrap;
    color: var(--tab-text); font-size: 14px; font-weight: 500; letter-spacing: 0.3px;
  }
  .card-back .brand-lockup { left: 150px; top: 104px; color: #ffffff; }
  .card-back .brand-name { font-size: 64px; }
  .card-back .brand-suffix { font-size: 14px; margin-top: 2px; }
</style>
</head>
<body>

<section class="card card-front" aria-label="Card front">
  <div class="ornament" role="img" aria-label="Faint teal floral scroll ornament"></div>
  <div class="brand-lockup">
    <span class="brand-name">Lorabelle</span>
    <span class="brand-suffix">Co., LTD</span>
  </div>
  <div class="person">
    <div class="person-name">Nim Ferrasco</div>
    <div class="person-title">Creative Director</div>
  </div>
  <ul class="contacts">
    <li>
      <svg viewBox="0 0 12 12"><rect x="1" y="4" width="10" height="7" rx="1.5" fill="var(--teal)"/><path d="M2 4 Q6 0 10 4" stroke="var(--teal)" stroke-width="1.4" fill="none"/></svg>
      <span>02 631 48 97</span>
    </li>
    <li>
      <svg viewBox="0 0 12 12"><rect x="3" y="0.5" width="6" height="11" rx="1.2" fill="var(--teal)"/><rect x="4" y="2" width="4" height="6" fill="#fff"/></svg>
      <span>081 536 2947</span>
    </li>
    <li class="gap">
      <svg viewBox="0 0 12 12"><rect x="0.5" y="2" width="11" height="8" fill="var(--teal)"/><path d="M1 2.5 L6 7 L11 2.5" stroke="#fff" stroke-width="1" fill="none"/></svg>
      <span>nim.ferrasco@lorabelle-example.com</span>
    </li>
    <li>
      <svg viewBox="0 0 12 12"><circle cx="6" cy="6" r="5.3" fill="var(--teal)"/><path d="M0.8 6 H11.2 M6 0.8 V11.2 M6 0.8 Q2.5 6 6 11.2 M6 0.8 Q9.5 6 6 11.2" stroke="#fff" stroke-width="0.8" fill="none"/></svg>
      <span>www.lorabelle-example.com</span>
    </li>
    <li>
      <svg viewBox="0 0 12 12"><circle cx="6" cy="6" r="5" fill="var(--teal)"/></svg>
      <span>Instagram: lorabelle_label</span>
    </li>
    <li>
      <svg viewBox="0 0 12 12"><rect x="1" y="1" width="10" height="10" fill="var(--teal)"/></svg>
      <span>Facebook: lorabelle</span>
    </li>
    <li class="gap">
      <svg viewBox="0 0 12 12"><path d="M6 11.5 C2 7 2 5.5 2 4.5 A4 4 0 0 1 10 4.5 C10 5.5 10 7 6 11.5 Z" fill="var(--teal)"/><circle cx="6" cy="4.5" r="1.5" fill="#fff"/></svg>
      <span>42 Maple Row, 2nd Floor , D Building , Thonrak , Chaloemrat 28.<br>East Sanphet , Rattana , Bangkok 10240 Thailand</span>
    </li>
  </ul>
</section>

<section class="card card-back" aria-label="Card back">
  <div class="ornament" role="img" aria-label="Light floral scroll ornament on teal"></div>
  <div class="tagline-tab">
    <span class="tagline">Glamour – Sophistication – Unique</span>
  </div>
  <div class="brand-lockup">
    <span class="brand-name">Lorabelle</span>
    <span class="brand-suffix">Co., LTD</span>
  </div>
</section>

</body>
</html>
```